Business Card Design for Varomir Facility Services

We are looking for a Business Card Design for the Company "Varomir Facility Services."
Front side:
- Company Logo (small)
- Company Name, address, pohone, website and personal data.
- white background, for text e.g. company colors (blue or green like in the logo)
Please use following data:
Company data:
Varomir Facility Services Kostelac
Birkenhaldweg 14
6347 Brunnwil
www.varomir-fs.ch
Person data:
Tarik Kostelac
Geschäftsführer
+41 76 519 47 83
info@varomir-fs.ch
Back side:
could be colored in blue or green
please use a big logo sing and some smaller icons to say what is all beeing offered in facility services, like cleaning, maintenance cleaning
industrial cleaning, caretaking, gardening, disposal. There is no need for everyone of the icons if there are similar or an icon is standing for more of them.
colors to use:
blue: HEX 246BB0
green: HEX 52B33E

```html
<!DOCTYPE html>
<html lang="de">
<head>
<meta charset="utf-8">
<title>Varomir Facility Services – Visitenkarte</title>
<link href="https://fonts.googleapis.com/css2?family=Montserrat:wght@400;500;700&display=swap" rel="stylesheet">
<style>
  :root {
    --brand-blue: #246BB0;
    --brand-green: #52B33E;
    --stripe-green: #1FA84A;
    --text-grey: #6a6a6a;
    --paper: #ffffff;
    --backdrop: #2b2d30;
  }
  * { box-sizing: border-box; margin: 0; padding: 0; }
  html, body {
    width: 1200px; height: 900px; overflow: hidden;
    background: var(--backdrop);
    font-family: "Montserrat", Arial, sans-serif;
  }
  .canvas { position: relative; width: 1200px; height: 900px; }

  .card {
    position: absolute; width: 640px; height: 376px; overflow: hidden;
    box-shadow: 0 12px 30px rgba(0,0,0,.45);
  }

  /* back side */
  .card-back { left: 480px; top: 40px; background: var(--brand-blue); }
  .back-brand {
    position: absolute; left: 0; right: 0; top: 92px;
    display: flex; align-items: center; justify-content: center; gap: 14px;
  }
  .brand-dot { flex: none; width: 34px; height: 34px; border-radius: 50%; background: var(--brand-green); }
  .brand-name { font-weight: 500; font-size: 32px; letter-spacing: 1px; white-space: nowrap; }
  .back-brand .brand-name { color: var(--paper); }
  .services {
    position: absolute; left: 28px; right: 28px; top: 236px;
    display: flex; justify-content: space-between; list-style: none;
  }
  .service { display: flex; flex-direction: column; align-items: center; gap: 10px; }
  .service-icon {
    width: 44px; height: 44px; border-radius: 50%;
    background: radial-gradient(circle at 40% 35%, #6cc957, var(--brand-green));
  }
  .service-label { color: var(--paper); font-size: 14px; white-space: nowrap; }

  /* front side */
  .card-front { left: 100px; top: 470px; background: var(--paper); }
  .contact { position: absolute; left: 40px; top: 36px; width: 230px; }
  .person-name { color: var(--brand-blue); font-weight: 700; font-size: 19px; text-transform: uppercase; }
  .person-role { color: var(--text-grey); font-size: 15px; margin-top: 4px; }
  .line-item {
    display: flex; align-items: center; gap: 8px;
    color: var(--text-grey); font-size: 15px; margin-top: 4px;
  }
  .line-item svg { flex: none; }
  .divider { width: 160px; height: 1.5px; background: var(--brand-blue); margin: 14px 0 12px; }
  .company-name {
    color: var(--stripe-green); font-weight: 700; font-size: 16px;
    text-transform: uppercase; line-height: 1.25;
  }
  .address { color: var(--text-grey); font-size: 15px; margin-top: 6px; line-height: 1.3; font-style: normal; }
  .front-brand {
    position: absolute; right: 34px; top: 120px;
    display: flex; align-items: center; gap: 10px;
  }
  .front-brand .brand-name { color: var(--brand-blue); font-size: 21px; }
  .front-brand .brand-dot { width: 22px; height: 22px; }
  .wave { position: absolute; left: 0; bottom: 0; width: 640px; height: 120px; }
</style>
</head>
<body>
<main class="canvas">

  <section class="card card-back" aria-label="Rückseite">
    <div class="back-brand">
      <span class="brand-dot"></span>
      <span class="brand-name">Varomir Facility Services</span>
    </div>
    <ul class="services">
      <li class="service"><span class="service-icon" role="img" aria-label="Icon Unterhaltsreinigung"></span><span class="service-label">Maintenance cleaning</span></li>
      <li class="service"><span class="service-icon" role="img" aria-label="Icon Industriereinigung"></span><span class="service-label">Industrial cleaning</span></li>
      <li class="service"><span class="service-icon" role="img" aria-label="Icon Hauswartung"></span><span class="service-label">Caretaking</span></li>
      <li class="service"><span class="service-icon" role="img" aria-label="Icon Gartenpflege"></span><span class="service-label">Gardening</span></li>
      <li class="service"><span class="service-icon" role="img" aria-label="Icon Entsorgung"></span><span class="service-label">Disposal</span></li>
    </ul>
  </section>

  <section class="card card-front" aria-label="Vorderseite">
    <div class="contact">
      <h1 class="person-name">Tarik Kostelac</h1>
      <p class="person-role">Geschäftsführer</p>
      <p class="line-item">
        <svg width="13" height="13" viewBox="0 0 24 24"><path fill="#246BB0" d="M6.6 10.8a15 15 0 0 0 6.6 6.6l2.2-2.2a1 1 0 0 1 1-.25 11 11 0 0 0 3.6.6 1 1 0 0 1 1 1V20a1 1 0 0 1-1 1A17 17 0 0 1 3 4a1 1 0 0 1 1-1h3.5a1 1 0 0 1 1 1c0 1.25.2 2.45.6 3.6a1 1 0 0 1-.25 1z"/></svg>
        +41 76 519 47 83
      </p>
      <p class="line-item">
        <svg width="14" height="11" viewBox="0 0 24 18"><rect x="1" y="1" width="22" height="16" rx="2" fill="none" stroke="#246BB0" stroke-width="2.4"/><path d="M2 2l10 8 10-8" fill="none" stroke="#246BB0" stroke-width="2.4"/></svg>
        info@varomir-fs.ch
      </p>
      <div class="divider"></div>
      <h2 class="company-name">Varomir Facility<br>Services Kostelac</h2>
      <address class="address">Birkenhaldweg 14<br>6347 Brunnwil</address>
      <p class="line-item">
        <svg width="13" height="13" viewBox="0 0 24 24"><circle cx="12" cy="12" r="10" fill="none" stroke="#246BB0" stroke-width="2.4"/><path d="M2 12h20M12 2c3 3 3 17 0 20M12 2c-3 3-3 17 0 20" fill="none" stroke="#246BB0" stroke-width="2"/></svg>
        www.varomir-fs.ch
      </p>
    </div>
    <div class="front-brand">
      <span class="brand-dot"></span>
      <span class="brand-name">Varomir Facility Services</span>
    </div>
    <svg class="wave" viewBox="0 0 640 120" preserveAspectRatio="none" aria-hidden="true">
      <path d="M0 30 C200 90 450 90 640 10 L640 120 L0 120 Z" style="fill:var(--stripe-green)"/>
      <path d="M0 38 C200 100 450 100 640 22 L640 120 L0 120 Z" style="fill:var(--paper)"/>
      <path d="M0 44 C200 106 450 106 640 28 L640 120 L0 120 Z" style="fill:var(--brand-blue)"/>
    </svg>
  </section>

</main>
</body>
</html>
```